Dietary supplement, Clean and simple.

Hi,
I’d like to talk about the project,

About us:
We are a dietary supplement (Vitamins, Minerals, amino acids etc.) company.
The goal is to have about 25 products at the end of this year. However, for this goal to be achieved we need a good label design to make our products represent our company values.
I’ll be here every day supporting your questions, we are fully committed to making the highest/best quality/customer experience possible.

About the design and our values:
- Professional (We are in the industry of professionalism and expertise. I would love to show we are competent at this, Id. Like to have the labels looks like we have done our research.)
- Efficient (White spacing, good use of the space available.)
- Simple (Straight forward, in 5 seconds they have to know what the product they have is/how functions. We’re trying to simplify it for the consumer.
- No distractions (the only visually “distracting” factor can be the vector art.)

The guidelines:
The goal is to have a universal design, with one element that changes (Vector art). I’ll attach a file/multiple files I think can show some visuals on what I’m looking for, and what parts of the design I think are good/bad.

Label size: 69x155mm (Front is 77.5mm)

Design whatever you think fits our image. You’re the design expert, all I care about is that it fits our company standards/image.

Use this color/font.
Font: Sans Serif
Main company color is Mind green #237D62 (Use this color for something in the design.)

What I thought would be cool/might looks ugly, who knows:
1. The front of the label: Should have 1 vector art, preferably in the top right corner. (That looks good in multiple colors. The vector can have multiple areas to color, I would prefer 2 main colors in the vector art. The interchangeable colors are used for multiple kinds of products.)
2. Text/product information on the left. The text that will have to be displayed:
- Product name for instance “Magnesium + B6”
- Description for the product for instance “Magnesium with ginger taste”
- Company name or logo. (Add ® behind it. We are soon to be trademark registered.)
3. We need to show the "daily intake" amount on the front and also the amount in the complete bottle. For instance, “Daily intake 1 capsule, 60 capsules”.
• You don’t have to design the backside of the label. After I chose a design, I’d like to chat and give specific information on what areas need to be assigned where. (Too complex because of the law.)
Updates

Hi, Please make the deadline 31 days total. I want designers to have the time to design. And not be rushed to finish it.

I want to extend the deadline because i feel like a slightly more medical look would be interesting. Hope you can come up with something!!

Target Market(s)

Dietary supplement consumers

Industry/Entity Type

Dietary supplements

Font styles to use
Sans Serif

Colors

Designer to choose colors to be used in the design.

Requirements
Must have
• Trademark icon "®" has to be at the top right after the company logo(text of logo)/name.

```html
<!DOCTYPE html>
<html lang="en">
<head>
<meta charset="utf-8">
<title>Calm Crest – Magnesium + B6 Label</title>
<link href="https://fonts.googleapis.com/css2?family=IBM+Plex+Sans:wght@400;500;600&family=Roboto+Condensed:wght@400;700&family=Montserrat:wght@800&display=swap" rel="stylesheet">
<style>
  :root {
    --mind-green: #237D62;
    --ink: #1d1d22;
    --rule: #1d1d22;
    --paper: #ffffff;
    --grad-pink: #f0a9bd;
    --grad-mauve: #a784a9;
    --grad-indigo: #5b63ae;
  }
  * { margin: 0; padding: 0; box-sizing: border-box; }
  html, body { width: 1200px; height: 1200px; overflow: hidden; background: var(--paper); }
  body { position: relative; font-family: "IBM Plex Sans", sans-serif; color: var(--ink); }

  .abs { position: absolute; }

  /* ---------- Front panel ---------- */
  .art-panel {
    left: 78px; top: 367px; width: 156px; height: 194px;
    background: linear-gradient(180deg, var(--grad-pink) 0%, var(--grad-mauve) 50%, var(--grad-indigo) 100%);
  }
  .brand-line { font-weight: 400; font-size: 23px; letter-spacing: 0.3px; line-height: 1; }
  .brand-line sup { font-size: 12px; vertical-align: top; position: relative; top: -2px; margin-left: 4px; }
  .front-brand { left: 78px; top: 884px; top: 884px; }
  .front-title { left: 78px; top: 616px; font-size: 43px; font-weight: 600; line-height: 1; letter-spacing: 0.2px; }
  .accent-rule {
    left: 78px; top: 687px; width: 156px; height: 3px;
    background: linear-gradient(90deg, var(--grad-pink), var(--grad-indigo));
  }
  .front-desc { left: 78px; top: 706px; font-size: 24px; font-weight: 400; line-height: 30px; }
  .dashed { height: 0; border-top: 1.5px dashed var(--mind-green); }
  .front-dash { left: 78px; top: 807px; width: 449px; }

  .capsule-icon { left: 78px; top: 826px; width: 19px; height: 39px; }
  .count { left: 107px; top: 828px; line-height: 17px; font-size: 14px; }
  .count b { color: var(--mind-green); font-weight: 600; font-size: 15px; display: block; }
  .intake { right: 684px; top: 828px; text-align: right; line-height: 17px; font-size: 14px; }
  .intake b { color: var(--mind-green); font-weight: 600; display: block; }
  .intake-bar { left: 526px; top: 826px; width: 1.5px; height: 39px; background: var(--mind-green); }

  .wordmark {
    color: var(--mind-green); font-weight: 600; font-size: 22px;
    letter-spacing: 1px; line-height: 1; white-space: nowrap;
  }
  .front-mark { left: 437px; top: 410px; }

  /* ---------- Back panel ---------- */
  .back-bar {
    left: 828px; top: 367px; width: 156px; height: 19px;
    background: linear-gradient(90deg, var(--grad-pink), var(--grad-mauve), var(--grad-indigo));
  }
  .back-head { left: 681px; width: 449px; text-align: center; }
  .back-brand { top: 404px; font-size: 16px; }
  .back-brand sup { font-size: 9px; }
  .back-title { top: 426px; font-size: 25px; font-weight: 500; line-height: 1; }
  .back-dash { left: 681px; top: 464px; width: 449px; }
  .back-mark { left: 906px; top: 847px; transform: translateX(-50%); }

  /* ---------- Supplement facts ---------- */
  .facts {
    border: 1.5px solid var(--rule); padding: 3px 5px 2px;
    font-family: "Roboto Condensed", sans-serif; font-size: 12px; line-height: 15px;
    background: var(--paper);
  }
  .facts-title { font-family: "Montserrat", sans-serif; font-weight: 800; font-size: 15px; letter-spacing: 1.4px; line-height: 17px; }
  .facts-row { display: flex; justify-content: space-between; }
  .facts-rule-thick { border-top: 2.5px solid var(--rule); margin: 2px 0; }
  .facts-rule { border-top: 1px solid var(--rule); margin: 2px 0; }
  .facts-head { font-weight: 700; font-size: 12.5px; }
  .facts-nutrient .amt { display: flex; gap: 22px; }
  .indent { padding-left: 9px; }
  .facts-a { left: 684px; top: 490px; width: 302px; height: 123px; }
  .facts-b { left: 685px; top: 662px; width: 302px; height: 123px; }
  .other { left: 683px; top: 617px; width: 300px; font-family: "Roboto Condensed", sans-serif; font-size: 12px; line-height: 15px; }

  .facts-vertical-frame { left: 1004px; top: 490px; width: 121px; height: 295px; border: 1.5px solid var(--rule); }
  .facts-vertical {
    left: -88px; top: 87px; width: 295px; height: 121px;
    transform: rotate(-90deg); border: none; padding: 2px 6px;
  }
  .facts-vertical .facts-nutrient .amt { gap: 14px; }
</style>
</head>
<body>

  <!-- Front label -->
  <div class="abs art-panel" role="img" aria-label="Interchangeable product vector art area"></div>
  <div class="abs brand-line" style="left:78px; top:584px;">CALM CREST<sup>®</sup></div>
  <div class="abs front-title">Magnesium + B6</div>
  <div class="abs accent-rule"></div>
  <div class="abs front-desc">Magnesium with<br>ginger taste</div>
  <div class="abs dashed front-dash"></div>

  <svg class="abs capsule-icon" viewBox="0 0 19 39" aria-hidden="true">
    <rect x="0.9" y="0.9" width="17.2" height="37.2" rx="8.6" fill="none" stroke="#237D62" stroke-width="1.6"/>
    <line x1="0.9" y1="19.5" x2="18.1" y2="19.5" stroke="#237D62" stroke-width="1.6"/>
  </svg>
  <div class="abs count"><b>60</b>CAPSULES</div>
  <div class="abs intake">DAILY INTAKE<b>1 CAPSULE</b></div>
  <div class="abs intake-bar"></div>

  <div class="abs wordmark front-mark">CALM CREST</div>

  <!-- Back label -->
  <div class="abs back-bar"></div>
  <div class="abs back-head brand-line back-brand">CALM CREST<sup>®</sup></div>
  <div class="abs back-head back-title">Magnesium + B6</div>
  <div class="abs dashed back-dash"></div>

  <div class="abs facts facts-a">
    <div class="facts-title">SUPPLEMENT FACTS</div>
    <div>Serving Size: One Capsule</div>
    <div class="facts-rule-thick"></div>
    <div class="facts-row facts-head"><span>One Capsule Contains:</span><span>%DV</span></div>
    <div class="facts-rule"></div>
    <div>Folate (1 mg as</div>
    <div class="facts-row facts-nutrient"><span class="indent">L-5-Methyltetrahydrofolate†)</span><span class="amt"><span>1.7 mg DFE</span><span>425%</span></span></div>
    <div class="facts-rule-thick"></div>
    <div>Daily Value (DV)</div>
  </div>

  <div class="abs other">Other Ingredients: Microcrystalline Cellulose, Hypromellose (derived from cellulose) capsule, Leucine, Silicon Dioxide.</div>

  <div class="abs facts facts-b">
    <div class="facts-title">SUPPLEMENT FACTS</div>
    <div>Serving Size: One Capsule</div>
    <div class="facts-rule-thick"></div>
    <div class="facts-row facts-head"><span>One Capsule Contains:</span><span>%DV</span></div>
    <div class="facts-rule"></div>
    <div>Folate (1 mg as</div>
    <div class="facts-row facts-nutrient"><span class="indent">L-5-Methyltetrahydrofolate†)</span><span class="amt"><span>1.7 mg DFE</span><span>425%</span></span></div>
    <div class="facts-rule-thick"></div>
    <div>Daily Value (DV)</div>
  </div>

  <div class="abs facts-vertical-frame">
    <div class="abs facts facts-vertical">
      <div class="facts-title">SUPPLEMENT FACTS</div>
      <div>Serving Size: One Capsule</div>
      <div class="facts-rule-thick"></div>
      <div class="facts-row facts-head"><span>One Capsule Contains:</span><span>%DV</span></div>
      <div class="facts-rule"></div>
      <div>Folate (1 mg as</div>
      <div class="facts-row facts-nutrient"><span class="indent">L-5-Methyltetrahydrofolate†)</span><span class="amt"><span>1.7 mg DFE</span><span>425%</span></span></div>
      <div class="facts-rule-thick"></div>
      <div>Daily Value (DV)</div>
    </div>
  </div>

  <div class="abs wordmark back-mark">CALM CREST</div>

</body>
</html>
```